Equine Podcast Cover Art Design

We need catchy cover art for a horse related podcast "Ride Onward Together"
Brief show description"
Whether you want to ride to experience horses, develop yourself to the next level as a horseman/horsewoman or ride to improve your physical and mental health, we are committed to helping you Ride Onward TogetherĀ®. Join us as we explore the nuance of equine management and sports as well as interview industry professionals to provide you with the knowledge necessary to be a better partner for your equine friends.
I have uploaded two existing logos we use for various purposes to give you an idea of existing style.
Target Market(s)
Horse owners and other equine professionals
Look and feel
Each slider illustrates characteristics of the customer's brand and the style your logo design should communicate.

```html
<!DOCTYPE html>
<html lang="en">
<head>
<meta charset="utf-8">
<title>Ride Onward Together® Podcast Cover</title>
<link href="https://fonts.googleapis.com/css2?family=Bebas+Neue&family=Great+Vibes&family=Montserrat:wght@500;700&display=swap" rel="stylesheet">
<style>
  :root {
    --forest: #08251a;
    --gold: #b3a46a;
    --white: #ffffff;
    --ink: #0c1f16;
  }
  * { margin: 0; padding: 0; box-sizing: border-box; }
  html, body { width: 1200px; height: 1200px; overflow: hidden; background: var(--forest); }
  .cover {
    position: relative;
    width: 1200px;
    height: 1200px;
    background: var(--forest);
    overflow: hidden;
  }
  .cover-photo {
    position: absolute;
    left: 726px;
    top: 0;
    width: 474px;
    height: 1200px;
    background:
      radial-gradient(ellipse at 70% 60%, #1a1310 0%, #2a1f19 30%, rgba(42,31,25,0) 60%),
      linear-gradient(180deg, #d6e4a4 0%, #a9c46a 22%, #7d9a48 40%, #5a6e3c 60%, #3f5a44 80%, #2f3a2c 100%);
  }
  .frame-line {
    position: absolute;
    left: 68px;
    top: 68px;
    width: 1065px;
    height: 1065px;
    border: 1px solid rgba(255,255,255,0.85);
    pointer-events: none;
  }
  .title {
    position: absolute;
    left: 40px;
    width: 660px;
    text-align: center;
    font-family: "Bebas Neue", "Oswald", sans-serif;
    color: var(--white);
    line-height: 1;
  }
  .title-ride { top: 140px; font-size: 190px; }
  .title-together { top: 570px; font-size: 172px; }
  .title-together .reg { font-size: 80px; vertical-align: 68px; margin-left: 4px; }
  .title-script {
    position: absolute;
    left: 40px;
    top: 360px;
    width: 660px;
    text-align: center;
    font-family: "Great Vibes", cursive;
    font-size: 170px;
    color: var(--gold);
    line-height: 1;
  }
  .podcast-label {
    position: absolute;
    left: 157px;
    top: 845px;
    width: 429px;
    height: 65px;
    background: var(--gold);
    display: flex;
    align-items: center;
    justify-content: center;
    font-family: "Montserrat", sans-serif;
    font-weight: 500;
    font-size: 34px;
    letter-spacing: 0.55em;
    padding-left: 0.55em;
    color: var(--ink);
  }
  .farm-mark {
    position: absolute;
    left: 157px;
    top: 1000px;
    width: 429px;
    display: flex;
    align-items: center;
    justify-content: center;
    gap: 14px;
    font-family: "Montserrat", sans-serif;
    font-weight: 700;
    font-size: 26px;
    letter-spacing: 0.04em;
    color: var(--white);
    text-transform: uppercase;
  }
  .farm-mark .dot {
    width: 22px;
    height: 22px;
    border-radius: 50%;
    background: var(--white);
  }
</style>
</head>
<body>
  <main class="cover">
    <div class="cover-photo" role="img" aria-label="Photo of a woman in a green plaid shirt leaning her head against a dark horse in a sunlit green meadow"></div>
    <div class="frame-line"></div>

    <h1>
      <span class="title title-ride">RIDE</span>
      <span class="title-script">onward</span>
      <span class="title title-together">TOGETHER<span class="reg">®</span></span>
    </h1>

    <div class="podcast-label">PODCAST</div>

    <div class="farm-mark"><span class="dot"></span>Hollow Creek Farm</div>
  </main>
</body>
</html>
```